Business Card Design

We have recently seen two business cards that caught our attention and think the designs would work for us. We are an accounting firm that serves small businesses in a variety of industries. Attached are the two business card that inspired us along with very rough layouts. We would like to see a professional layout using our company information.

Industry/Entity Type

Accounting

Contact Information for Business Card

Company Name - Marlowe Thistle
Address - 4182 Orlanby Lane, Suite 610, Houston, TX 77093
713-555-0187 - Main
281-555-0342 - Fax

Team Member Names, emails and phone numbers (see attachment)

```html
<!DOCTYPE html>
<html lang="en">
<head>
<meta charset="utf-8">
<title>Marlowe Thistle – Business Card</title>
<link rel="stylesheet" href="https://fonts.googleapis.com/css2?family=Lato:wght@400;700;900&display=swap">
<style>
  :root {
    --backdrop: #2b2b2b;
    --card: #f7f7f7;
    --card-shade: #e6e6e6;
    --ink: #151515;
    --muted: #9a9a9a;
  }
  * { margin: 0; padding: 0; box-sizing: border-box; }
  html, body {
    width: 1200px; height: 900px; overflow: hidden;
    background: var(--backdrop);
    font-family: "Lato", sans-serif;
    color: var(--ink);
  }
  .card {
    position: absolute; left: 100px; top: 164px;
    width: 1000px; height: 572px;
    border-radius: 30px;
    background: linear-gradient(135deg, var(--card) 0%, #ffffff 45%, var(--card-shade) 100%);
  }
  .brand-name {
    position: absolute; left: 70px; top: 150px;
    font-weight: 900; font-size: 34px; letter-spacing: 1px;
    text-transform: uppercase;
  }
  .divider {
    position: absolute; left: 70px; right: 60px; top: 222px;
    height: 3px; background: var(--ink);
  }
  .member {
    position: absolute; right: 60px; top: 170px; text-align: right;
  }
  .member-name {
    font-weight: 900; font-size: 38px; letter-spacing: 0.5px;
    text-transform: uppercase; line-height: 48px;
  }
  .member-details {
    position: absolute; right: 60px; top: 234px; text-align: right;
  }
  .member-role {
    font-size: 22px; letter-spacing: 1.5px; color: var(--muted);
    text-transform: uppercase;
  }
  .contact-line {
    display: flex; align-items: center; justify-content: flex-end; gap: 10px;
    font-weight: 700; font-size: 24px; margin-top: 6px;
  }
  .contact-line.email { margin-top: 34px; }
  .icon { width: 24px; height: 24px; fill: var(--ink); flex: none; }
  .company {
    position: absolute; left: 0; right: 0; top: 372px; text-align: center;
  }
  .company-name {
    font-weight: 900; font-size: 48px; letter-spacing: 1px;
    text-transform: uppercase;
  }
  .company-row {
    display: flex; justify-content: center; align-items: center; gap: 14px;
    font-weight: 700; font-size: 28px; margin-top: 10px;
  }
  .company-row .gap { width: 36px; }
  .company-row .icon { width: 30px; height: 30px; }
</style>
</head>
<body>
  <section class="card">
    <div class="brand-name">Marlowe Thistle</div>

    <div class="member">
      <div class="member-name">Delphine Arkwright</div>
    </div>
    <div class="divider"></div>

    <div class="member-details">
      <div class="member-role">Account Manager</div>
      <div class="contact-line">
        <svg class="icon" viewBox="0 0 24 24" aria-hidden="true"><path d="M7 1h10a2 2 0 0 1 2 2v18a2 2 0 0 1-2 2H7a2 2 0 0 1-2-2V3a2 2 0 0 1 2-2zm0 3v14h10V4zm5 15.5a1 1 0 1 0 0 2 1 1 0 0 0 0-2z"/></svg>
        <span>832-555-0129</span>
      </div>
      <div class="contact-line email">
        <svg class="icon" viewBox="0 0 24 24" aria-hidden="true"><path d="M2 5h20v14H2zm2 2v.5l8 5.5 8-5.5V7zm0 3v7h16v-7l-8 5.5z"/></svg>
        <span>darkwright@marlowethistle.com</span>
      </div>
    </div>

    <div class="company">
      <div class="company-name">Marlowe Thistle</div>
      <div class="company-row">
        <svg class="icon" viewBox="0 0 24 24" aria-hidden="true"><path d="M2 8c0-3 4-5 10-5s10 2 10 5v2h-5V8c-1-1-3-1.5-5-1.5S8 7 7 8v2H2zm5 3h10l3 8H4zm5 2a2.5 2.5 0 1 0 0 5 2.5 2.5 0 0 0 0-5z"/></svg>
        <span>713-555-0187</span>
        <span class="gap"></span>
        <svg class="icon" viewBox="0 0 24 24" aria-hidden="true"><path d="M6 2h10l2 2v5H6zm-4 8h20v8h-4v-3H6v3H2zm5 7h10v5H7z"/></svg>
        <span>281-555-0342</span>
      </div>
      <div class="company-row">
        <svg class="icon" viewBox="0 0 24 24" aria-hidden="true"><path d="M12 3l10 9h-3v9h-5v-6h-4v6H5v-9H2z"/></svg>
        <span>4182 Orlanby Lane, Suite 610, Houston, TX 77093</span>
      </div>
    </div>
  </section>
</body>
</html>
```